New Website for novelty yarn producer

We need a new website for our company, Vedrana. We make highly tailored yarns for weavers worldwide. This year marks our 40th anniversary and we want to evolve our image and identity.

Our temporary website can be found at:
www.vedranathreads.example

Our only concern in that throughout the website the protagonist must be our client, we make their creations possible and are highly adaptable both during the ideation process of the yarn as well as in the production. This is at the core of the way we do business and is summarised within the concept of FMC (Full Motion Craft).

Industry/Entity Type

Textile

Number of Pages Required

1 page

Colors
9bcb3c

Requirements
Must have
• Full Motion Craft (FMC) - can be found on or current website www.vedranathreads.example

```html
<!DOCTYPE html>
<html lang="en">
<head>
<meta charset="utf-8">
<title>Vedrana – Novelty Yarn Solutions</title>
<link href="https://fonts.googleapis.com/css2?family=Kreon:wght@300;400&family=Merriweather:wght@300;400;700&display=swap" rel="stylesheet">
<style>
:root{
  --green:#8cc43a;
  --green-line:#9bcb3c;
  --ink:#1c1c1c;
  --muted:#6b6b6b;
  --paper:#f1f1f0;
  --white:#ffffff;
  --dash:#bdbdbd;
}
*{box-sizing:border-box;margin:0;padding:0}
html,body{width:1200px;height:2219px;overflow:hidden}
body{font-family:"Merriweather",Georgia,serif;color:var(--ink);background:var(--white);position:relative}
.section{position:absolute;left:0;width:1200px}
.btn{position:absolute;left:516px;width:169px;height:40px;background:var(--green);color:var(--white);
  font-size:10px;font-weight:700;letter-spacing:.5px;text-transform:uppercase;display:flex;align-items:center;justify-content:center}

/* hero */
.hero{top:0;height:521px;overflow:hidden;background:linear-gradient(160deg,#3b3a3a 0%,#6a6f78 40%,#8e8f98 60%,#5a4c44 85%,#2d2622 100%)}
.hero-photo{position:absolute;inset:0;background:radial-gradient(ellipse at 70% 35%,rgba(210,200,190,.35),transparent 55%),radial-gradient(ellipse at 90% 10%,rgba(190,110,50,.45),transparent 40%)}
.brand{position:absolute;left:74px;top:20px;font-family:"Kreon",Georgia,serif;font-size:42px;font-weight:400;color:var(--white);letter-spacing:1px}
.nav{position:absolute;right:35px;top:0;display:flex;gap:29px;height:93px;align-items:center}
.nav a{color:var(--white);font-size:12px;text-decoration:none;text-transform:uppercase;position:relative}
.nav a.active::before{content:"";position:absolute;left:-8px;right:-8px;top:-39px;height:5px;background:var(--green)}
.hero-rule{position:absolute;left:0;right:0;top:93px;border-top:1px dashed rgba(255,255,255,.5)}
.badge{position:absolute;left:534px;top:183px;width:132px;height:132px;border:2px solid var(--white);border-radius:50%;color:var(--white);text-align:center}
.badge .num{font-family:"Kreon",Georgia,serif;font-size:58px;line-height:1;margin-top:22px;display:block}
.badge .name{font-family:"Kreon",Georgia,serif;font-size:15px;display:block}
.hero-title{position:absolute;left:334px;width:532px;top:331px;height:51px;border-top:1px dashed rgba(255,255,255,.55);border-bottom:1px dashed rgba(255,255,255,.55);
  color:var(--white);font-family:"Kreon",Georgia,serif;font-size:34px;font-weight:300;text-align:center;line-height:49px}
.hero .btn{top:397px}

/* features */
.features{top:521px;height:305px;background:var(--paper);border-top:1px dashed var(--dash);border-bottom:1px dashed var(--dash)}
.feature{position:absolute;top:0;width:300px;text-align:center}
.feature .icon{position:absolute;left:103px;top:30px;width:94px;height:94px;border-radius:50%;border:2px solid var(--green-line);background:#e4e4e2}
.feature .icon.dark{border-color:#222}
.feature h3{position:absolute;left:39px;width:222px;top:136px;height:47px;border-top:1px solid var(--green-line);border-bottom:1px solid var(--green-line);
  font-family:"Kreon",Georgia,serif;font-weight:400;font-size:22px;line-height:45px;text-transform:uppercase}
.feature p{position:absolute;left:0;width:300px;top:196px;font-size:12.5px;line-height:22px;color:var(--muted)}

/* fmc */
.fmc{top:826px;height:367px;background:var(--white);text-align:center}
.fmc-name{position:absolute;left:0;right:0;top:100px;font-family:"Kreon",Georgia,serif;font-weight:400;font-size:24px;letter-spacing:3px;color:var(--ink);text-transform:uppercase}
.fmc h2{position:absolute;left:0;right:0;top:188px;font-family:"Kreon",Georgia,serif;font-weight:400;font-size:29px;text-transform:uppercase}
.fmc p{position:absolute;left:350px;width:500px;top:230px;font-size:12.5px;line-height:20px;color:var(--muted)}
.fmc .btn{top:287px}

/* team */
.team{top:1193px;height:305px;background:var(--paper);border-top:1px dashed var(--dash);text-align:center}
.team .lead{position:absolute;left:215px;width:770px;top:80px;font-size:18px;line-height:28px}
.team .focus{position:absolute;left:0;right:0;top:181px;font-size:12px;font-weight:700}
.team .btn{top:219px}

/* numbers */
.numbers{top:1498px;height:478px;overflow:hidden;background:linear-gradient(90deg,#15181b 0%,#2b2724 45%,#3a332c 70%,#1b1816 100%)}
.numbers-photo{position:absolute;inset:0;background:radial-gradient(ellipse at 55% 40%,rgba(120,110,95,.35),transparent 60%)}
.numbers h2{position:absolute;left:488px;width:222px;top:80px;height:47px;border-top:1px solid rgba(255,255,255,.8);border-bottom:1px solid rgba(255,255,255,.8);
  font-family:"Kreon",Georgia,serif;font-weight:300;font-size:27px;color:var(--white);text-align:center;line-height:45px;text-transform:uppercase}
.stat{position:absolute;top:159px;width:184px;height:184px;border-radius:50%;border:2px solid rgba(255,255,255,.85);color:var(--white);text-align:center}
.stat .value{display:block;font-family:"Kreon",Georgia,serif;font-weight:300;font-size:96px;line-height:1;color:var(--green);margin-top:22px}
.stat .unit{display:block;font-family:"Kreon",Georgia,serif;font-weight:300;font-size:18px;line-height:18px}
.numbers .btn{top:370px}

/* footer */
.footer{top:1976px;height:243px;background:var(--paper);border-top:1px dashed var(--dash)}
.footer .brand-foot{position:absolute;left:52px;top:52px;font-family:"Kreon",Georgia,serif;font-size:44px;color:var(--ink)}
.footer ul{position:absolute;left:295px;top:50px;list-style:none}
.footer li{font-size:12px;line-height:18px;text-transform:uppercase}
.contact{position:absolute;left:516px;font-size:11.5px;line-height:18px;text-transform:uppercase}
.contact svg{position:absolute;left:0;top:2px}
.contact span{display:block;padding-left:24px}
.legal{position:absolute;left:827px;top:50px;font-size:11.5px;line-height:18px;text-transform:uppercase}
.footer-rule{position:absolute;left:0;right:0;top:196px;border-top:1px dashed var(--dash)}
.copyright{position:absolute;left:0;right:0;top:213px;text-align:center;font-size:11.5px;text-transform:uppercase}
.version{position:absolute;right:36px;top:213px;font-size:11.5px}
</style>
</head>
<body>

<section class="section hero">
  <div class="hero-photo" role="img" aria-label="Close-up photo of a sewing machine foot stitching woven fabric"></div>
  <div class="brand">Vedrana</div>
  <nav class="nav">
    <a class="active" href="#">Home</a>
    <a href="#">About us</a>
    <a href="#">Full Motion Craft</a>
    <a href="#">Heritage</a>
    <a href="#">Team</a>
    <a href="#">Blog</a>
    <a href="#">Contact</a>
  </nav>
  <div class="hero-rule"></div>
  <div class="badge"><span class="num">40</span><span class="name">Vedrana</span></div>
  <h1 class="hero-title">TAILORED WEAVING SOLUTIONS</h1>
  <a class="btn">Learn more</a>
</section>

<section class="section features">
  <div class="feature" style="left:75px">
    <div class="icon" role="img" aria-label="Sewing machine icon"></div>
    <h3>Experience</h3>
    <p>Over the years the company has gained the knowledge and skills that define the superiority of our product and the rigor of our work ethic</p>
  </div>
  <div class="feature" style="left:450px">
    <div class="icon dark" role="img" aria-label="Needle and thread icon"></div>
    <h3>Creativity</h3>
    <p>Over the years the company has gained the knowledge and skills that define the superiority of our product and the rigor of our work ethic</p>
  </div>
  <div class="feature" style="left:809px">
    <div class="icon dark" role="img" aria-label="Dress icon"></div>
    <h3>Professionality</h3>
    <p>Over the years the company has gained the knowledge and skills that define the superiority of our product and the rigor of our work ethic</p>
  </div>
</section>

<section class="section fmc">
  <div class="fmc-name">Full Motion Craft</div>
  <h2>Production built around you</h2>
  <p>Versatility and flexibility both in development and production are key in delivering a custom solution capable of giving life to your products.</p>
  <a class="btn">Find out more</a>
</section>

<section class="section team">
  <p class="lead">Our team has decades of experience in providing yarn solutions to weavers around the world, assisting them in the creation of outstanding textiles. Our clients can expect open lines of communication, clarity and professionality</p>
  <p class="focus">Our focus is our client. The success of a client is our success.</p>
  <a class="btn">Our heritage</a>
</section>

<section class="section numbers">
  <div class="numbers-photo" role="img" aria-label="Photo of a man in a tailored tweed jacket and bow tie"></div>
  <h2>VYS in numbers</h2>
  <div class="stat" style="left:229px"><span class="value">40</span><span class="unit">Years In Business</span></div>
  <div class="stat" style="left:508px"><span class="value">2</span><span class="unit">Million<br>Kilograms/Yr</span></div>
  <div class="stat" style="left:787px"><span class="value">8</span><span class="unit">Brands</span></div>
  <a class="btn">Our heritage</a>
</section>

<footer class="section footer">
  <div class="brand-foot">Vedrana</div>
  <ul>
    <li>&nbsp;Home</li><li>About us</li><li>Full Motion Craft</li><li>Heritage</li><li>Team</li><li>Blog</li><li>Contact</li>
  </ul>
  <div class="contact" style="top:50px">
    <svg width="12" height="16" viewBox="0 0 12 16"><path d="M6 0C2.7 0 0 2.6 0 5.9 0 10.3 6 16 6 16s6-5.7 6-10.1C12 2.6 9.3 0 6 0zm0 8.3A2.4 2.4 0 1 1 6 3.5a2.4 2.4 0 0 1 0 4.8z" fill="#8cc43a"/></svg>
    <span>Vedrana Novelty Yarn Solutions</span>
    <span>Corvane S.R.L Via dei Telai</span>
    <span>14 - 00000 Borgo Lana - Italy</span>
  </div>
  <div class="contact" style="top:121px">
    <svg width="14" height="14" viewBox="0 0 14 14"><path d="M3 0l2.5 3.5-1.5 2c.8 1.7 2.4 3.3 4.5 4.5l2-1.5L14 11l-1.5 2.6C6.5 14.5-.5 7.5.4 1.5z" fill="#8cc43a"/></svg>
    <span>Tel. 0100 200300 R.A &nbsp;| &nbsp;Fax 0100 200301</span>
  </div>
  <div class="legal">
    R.E.A BL 100200 - Reg. Imp. BL 01234567890<br>
    P. IVA 09876543210 - Cod. Fisc. 01234567890<br>
    Capitale Sociale € 50.000,00 Int. Ver.
  </div>
  <div class="footer-rule"></div>
  <p class="copyright">© 2018 Company Name | All rights reserved</p>
  <span class="version">C5</span>
</footer>

</body>
</html>
```